Design of a nice Video On Demand Website

We are looking to design a nice Website for our Video On demand platform we are getting ready to launch. We have put together a file to illustrate the idea and design concept we want. The file also has the menu sections ect. The Designers should look at the file and suggest design ideas based on the concept we put together on the file. The design should be clean yet simple so users can experience a better Navigation. The designer is free to choose whatever color he thinks fit.
Updates

Need extra days to review

Sick

Target Market(s)

Streaming

Number of Pages Required

1 page

Font styles to use
Sans Serif

Colors

Designer to choose colors to be used in the design.

Requirements
Must have
• I will let the designer choose what is best.
Nice to have
Should not have

```html
<!DOCTYPE html>
<html lang="en">
<head>
<meta charset="utf-8">
<title>Lumora TV – Packages &amp; Pricing</title>
<link rel="stylesheet" href="https://fonts.googleapis.com/css2?family=Ubuntu:wght@400;500;700&family=Poppins:wght@400;500&display=swap">
<style>
:root{
  --blue:#1387d1;
  --navy:#2a3a84;
  --band:#3a5fb0;
  --text:#333;
  --yellow:#f2c01f;
  --cyan:#00b8d4;
  --purple:#6a3ab8;
  --green:#04963f;
  --magenta:#c61fd4;
  --footer:#2e3340;
  --white:#fff;
}
*{margin:0;padding:0;box-sizing:border-box}
html,body{width:714px;height:1200px;overflow:hidden;background:var(--white)}
body{position:relative;font-family:Ubuntu,sans-serif;color:var(--text)}
.topbar{position:absolute;top:0;left:0;width:714px;height:26px;background:var(--blue);display:flex;justify-content:flex-end;align-items:center;gap:12px;padding-right:59px;color:var(--white);font-size:7.5px}
.topbar span,.call-line{display:flex;align-items:center;gap:5px}
.mark{display:inline-block;width:14px;height:10px;border-radius:1px}
.mark.us{background:linear-gradient(#b22234 0 50%,#fff 50%);}
.mark.ca{background:linear-gradient(90deg,#d52b1e 0 28%,#fff 28% 72%,#d52b1e 72%)}
.mark.msg{background:#4fbd5b;border-radius:2px}
.header{position:absolute;top:26px;left:0;width:714px;height:57px;display:flex;align-items:center;padding:0 59px;font-family:Poppins,sans-serif}
.brand{font-family:Ubuntu,sans-serif;font-weight:700;font-size:17px;color:var(--navy);display:flex;align-items:center;gap:5px}
.brand i{display:inline-block;width:9px;height:9px;background:var(--blue);border-radius:50%}
.nav{margin-left:auto;display:flex;gap:18px;align-items:center;font-size:8.5px;color:#222}
.nav .active{color:var(--blue)}
.signin{background:var(--blue);color:var(--white);border-radius:12px;padding:6px 14px;font-size:8px}
.hero{position:absolute;top:83px;left:0;width:714px;height:297px;background:linear-gradient(100deg,#b9b2a8 0%,#8a7468 35%,#9d8f86 60%,#c8c2bc 100%)}
.channels{position:absolute;top:380px;left:0;width:714px;height:77px;background:var(--band);display:flex;align-items:center;justify-content:center;gap:10px}
.arrow{width:19px;height:19px;border-radius:50%;background:rgba(255,255,255,.35);display:flex;align-items:center;justify-content:center}
.channel{width:43px;height:43px;border-radius:5px}
.section-title{position:absolute;top:484px;width:714px;text-align:center;font-size:17px;font-weight:700;color:var(--navy)}
.section-sub{position:absolute;top:517px;width:714px;text-align:center;font-size:8.5px}
.plan{position:absolute;width:138px;height:215px;border:1px solid #ddd;border-radius:3px;overflow:hidden;background:var(--white);text-align:center;font-size:8.5px;line-height:12px}
.plan-head{height:86px;color:var(--white);padding-top:22px}
.plan-name{font-size:11px;font-weight:500}
.plan-price{font-size:20px;font-weight:700;margin-top:6px}
.plan-feature{height:38px;display:flex;align-items:center;justify-content:center;padding:0 8px}
.plan-feature.alt{background:#f6f6f6;height:32px}
.plan-btn{display:inline-block;margin-top:13px;width:87px;height:23px;line-height:23px;border-radius:12px;color:var(--white);font-size:8px}
.yellow .plan-head,.yellow .plan-btn{background:var(--yellow)}
.cyan .plan-head,.cyan .plan-btn{background:var(--cyan)}
.purple .plan-head,.purple .plan-btn{background:var(--purple)}
.green .plan-head,.green .plan-btn{background:var(--green)}
.magenta .plan-head,.magenta .plan-btn{background:var(--magenta)}
.footer{position:absolute;top:1030px;left:0;width:714px;height:170px;background:var(--footer);color:var(--white);font-size:7.5px}
.footer h3{font-size:12px;font-weight:700;margin-bottom:12px}
.col{position:absolute;top:18px}
.links p{margin-bottom:10px}
.call-line{margin-bottom:12px}
.reach p{margin-bottom:14px}
.foot-brand{position:absolute;left:372px;top:62px;font-size:17px;font-weight:700;display:flex;align-items:center;gap:5px}
.foot-brand i{width:9px;height:9px;border-radius:50%;background:var(--blue);display:inline-block}
.bottom{position:absolute;left:0;top:138px;width:714px;border-top:1px solid #474c58;padding:14px 59px 0;display:flex;justify-content:space-between}
</style>
</head>
<body>
<div class="topbar">
  <span><i class="mark us"></i>(718) 555-0142</span>
  <span><i class="mark ca"></i>(514) 555-0187</span>
  <span><i class="mark msg"></i>(646) 555-0129</span>
</div>
<header class="header">
  <div class="brand"><i></i>Lumora TV</div>
  <nav class="nav">
    <span>What Is Lumora TV?</span>
    <span>Compatible Devices</span>
    <span class="active">Packages &amp; Pricing</span>
    <span>Video Tutorial</span>
    <span class="signin">SIGN IN</span>
  </nav>
</header>
<div class="hero" role="img" aria-label="Photo of a family smiling on a sofa while watching television"></div>
<div class="channels">
  <span class="arrow"><svg width="6" height="8" viewBox="0 0 6 8"><path d="M4 1L1 4l3 3" stroke="#fff" fill="none" stroke-width="1.2"/></svg></span>
  <span class="channel" style="background:#d8141e"></span>
  <span class="channel" style="background:#f4e400"></span>
  <span class="channel" style="background:#17a53c"></span>
  <span class="channel" style="background:#1a1a1a"></span>
  <span class="channel" style="background:#ffffff"></span>
  <span class="channel" style="background:#e8431d"></span>
  <span class="channel" style="background:#e4e4e4"></span>
  <span class="channel" style="background:#1d8fdc"></span>
  <span class="channel" style="background:#139c3a"></span>
  <span class="channel" style="background:#c8102e"></span>
  <span class="arrow"><svg width="6" height="8" viewBox="0 0 6 8"><path d="M2 1l3 3-3 3" stroke="#fff" fill="none" stroke-width="1.2"/></svg></span>
</div>
<h2 class="section-title">Packages &amp; Pricing</h2>
<p class="section-sub">African and International</p>

<div class="plan yellow" style="left:59px;top:551px">
  <div class="plan-head"><div class="plan-name">Monthly</div><div class="plan-price">$ 19.99</div></div>
  <div class="plan-feature">Enjoy over 270 African and International channels</div>
  <div class="plan-feature alt">+7 days DVR of your Favorite TV Shows.</div>
  <span class="plan-btn">SUBSCRIBE</span>
</div>
<div class="plan cyan" style="left:212px;top:551px">
  <div class="plan-head"><div class="plan-name">Quartely</div><div class="plan-price">$ 47.99</div></div>
  <div class="plan-feature">Enjoy over 270 African and International channels</div>
  <div class="plan-feature alt">+7 days DVR of your Favorite TV Shows.</div>
  <span class="plan-btn">SUBSCRIBE</span>
</div>
<div class="plan purple" style="left:365px;top:551px">
  <div class="plan-head"><div class="plan-name">Semi-Annual</div><div class="plan-price">$ 89.99</div></div>
  <div class="plan-feature">Enjoy over 270 African and International channels</div>
  <div class="plan-feature alt">+7 days DVR of your Favorite TV Shows.</div>
  <span class="plan-btn">SUBSCRIBE</span>
</div>
<div class="plan green" style="left:518px;top:551px">
  <div class="plan-head"><div class="plan-name">Annual Plan (Stick)</div><div class="plan-price">$ 127.99</div></div>
  <div class="plan-feature">Enjoy over 270 African &amp; International channels on Stick</div>
  <div class="plan-feature alt">+7 days DVR of your Favorite TV Shows.</div>
  <span class="plan-btn">SUBSCRIBE</span>
</div>
<div class="plan magenta" style="left:58px;top:781px">
  <div class="plan-head"><div class="plan-name">Annual Plan (Premium)</div><div class="plan-price">$ 159.99</div></div>
  <div class="plan-feature">Enjoy over 270 African and International channels</div>
  <div class="plan-feature alt">+7 days DVR of your Favorite TV Shows.</div>
  <span class="plan-btn">SUBSCRIBE</span>
</div>

<footer class="footer">
  <div class="col links" style="left:59px">
    <h3>Quick Links</h3>
    <p>What Is Lumora TV?</p><p>Compatible Devices</p><p>Packages &amp; Pricing</p><p>Video Tutorial</p>
  </div>
  <div class="col" style="left:196px">
    <h3>Call Us Now</h3>
    <div class="call-line"><i class="mark us" style="width:19px;height:14px"></i><b>USA:</b> (718) 555-0142</div>
    <div class="call-line"><i class="mark ca" style="width:19px;height:14px"></i><b>Canada:</b> (514) 555-0187</div>
    <div class="call-line"><i class="mark msg" style="width:19px;height:14px"></i><b>Messenger:</b> (646) 555-0129</div>
  </div>
  <div class="foot-brand"><i></i>Lumora TV</div>
  <div class="col reach" style="left:515px">
    <h3>Reach Us</h3>
    <p><b>Support:</b> support@lumoratv.example</p>
    <p><b>Email:</b> info@lumoratv.example</p>
    <p><b>Billing:</b> billing@lumoratv.example</p>
  </div>
  <div class="bottom">
    <span>© 2019 Lumora TV &nbsp;|&nbsp; All Rights Reserved</span>
    <span>Terms &amp; Conditions &nbsp;|&nbsp; Privacy Policy &nbsp;|&nbsp; Contact Us &nbsp;|&nbsp; FAQ</span>
  </div>
</footer>
</body>
</html>
```